A new presentation to our clients

we are a Real Estate agency, our website is www.lumibrasa.com and it’s time to have a new, fashion and remarcable Business Card. we want to differentiate ourselves from other companies so we want a business card that differentiates us. we want the business card to impact our customers. in the competitive market that we have today, we have to be different and it is this difference that we seek

Target Market(s)

Real Estate Clients

Contact Information for Business Card

We search a totaly diferent card from the usual

Font styles to use
Sans Serif

Colors
e34197

Requirements
Must have
• Logo, adress, phone contact, e-mail, photo, and our website
Nice to have
• We would like to see a modern business card
Should not have
• Houses or building draws

```html
<!DOCTYPE html>
<html lang="pt">
<head>
<meta charset="utf-8">
<title>Lumi Brasa – Business Card</title>
<link rel="stylesheet" href="https://fonts.googleapis.com/css2?family=Nunito+Sans:wght@400;700;800&display=swap">
<style>
  :root {
    --brand-pink: #e6306f;
    --ink-grey: #555659;
    --label-grey: #8a8a8c;
    --card-white: #ffffff;
    --backdrop: #e9e9ea;
  }
  html, body {
    margin: 0;
    padding: 0;
    width: 1200px;
    height: 791px;
    overflow: hidden;
    background: var(--backdrop);
    font-family: "Nunito Sans", Arial, sans-serif;
  }
  .card {
    position: absolute;
    left: 80px;
    top: 99px;
    width: 1040px;
    height: 593px;
    background: var(--card-white);
    border-radius: 36px;
    box-shadow: 0 6px 24px rgba(0,0,0,0.12);
  }
  .brand-name {
    position: absolute;
    right: 49px;
    top: 62px;
    margin: 0;
    font-size: 84px;
    font-weight: 700;
    color: var(--brand-pink);
    letter-spacing: 1px;
    line-height: 1;
  }
  .holder {
    position: absolute;
    left: 48px;
    top: 372px;
  }
  .holder-name {
    margin: 0;
    font-size: 36px;
    font-weight: 800;
    color: var(--brand-pink);
    line-height: 1.1;
  }
  .holder-role {
    margin: 2px 0 0;
    font-size: 24px;
    font-weight: 700;
    color: var(--label-grey);
    letter-spacing: 0.5px;
  }
  .divider {
    position: absolute;
    left: 48px;
    top: 462px;
    width: 943px;
    height: 2px;
    background: var(--brand-pink);
  }
  .contact {
    position: absolute;
    top: 490px;
    font-size: 22px;
    color: var(--ink-grey);
    line-height: 31px;
  }
  .contact p { margin: 0; display: flex; align-items: center; white-space: nowrap; }
  .contact svg { width: 22px; height: 22px; margin-right: 13px; fill: var(--brand-pink); }
  .contact-address { left: 48px; }
  .contact-phones { left: 413px; }
  .contact-online { left: 695px; }
</style>
</head>
<body>
  <main class="card">
    <h1 class="brand-name">Lumi Brasa</h1>

    <div class="holder">
      <h2 class="holder-name">RITA ALMEIDA</h2>
      <p class="holder-role">CEO/FOUNDER</p>
    </div>

    <div class="divider"></div>

    <address class="contact contact-address" style="font-style:normal">
      <p>Rua das Flores Altas, 118</p>
      <p>4050-262, Porto Ribeira Sul</p>
    </address>

    <div class="contact contact-phones">
      <p>
        <svg viewBox="0 0 24 24" aria-hidden="true"><path d="M6.6 10.8c1.4 2.8 3.8 5.1 6.6 6.6l2.2-2.2c.3-.3.7-.4 1-.2 1.1.4 2.3.6 3.6.6.6 0 1 .4 1 1V20c0 .6-.4 1-1 1C10.6 21 3 13.4 3 4c0-.6.4-1 1-1h3.5c.6 0 1 .4 1 1 0 1.3.2 2.5.6 3.6.1.3 0 .7-.2 1z"/></svg>
        (+351) 220 145 380
      </p>
      <p>
        <svg viewBox="0 0 24 24" aria-hidden="true"><path d="M7 3h10v5H7zM4 9h16a2 2 0 0 1 2 2v6h-4v4H6v-4H2v-6a2 2 0 0 1 2-2zm4 6v4h8v-4z"/></svg>
        (+351) 220 145 389
      </p>
    </div>

    <div class="contact contact-online">
      <p>
        <svg viewBox="0 0 24 24" aria-hidden="true"><path d="M2 5h20v14H2zm2 2v.5l8 5.5 8-5.5V7l-8 5.5z"/></svg>
        geral@lumibrasa.com
      </p>
      <p>
        <svg viewBox="0 0 24 24" aria-hidden="true"><circle cx="12" cy="12" r="10"/><path d="M8 6c2 1 1 3 3 4s0 3 1 4-1 3 0 5c-3-1-4-3-4-5s-2-2-2-4 1-3 2-4zM15 5c1 1 3 2 2 4s-2 1-2 3 2 2 3 2" fill="none" stroke="#fff" stroke-width="1.4"/></svg>
        www.lumibrasa.com
      </p>
    </div>
  </main>
</body>
</html>
```